Business Cards for Volmont Hayes, a law firm

We changed our firm's name from "Volmont & Hayes LLP" to "Volmont Hayes", we need to update our cards with a new design. We like the overall look of the back but the front side of the cards (see attached mockup) needs a refreshed look. I also attach our current logo so you can get rid of that LLP and &. We have a new address as well (not same as on mockup).

Target Market(s)

Clients of law firm

Industry/Entity Type

Law Firm

Contact Information for Business Card

Frontsides:

Lorenzo T. Volmont
Partner
Tel: (416) 555-0172 ext. 101
Fax: (647) 555-0139
Email: lvolmont@vhlegal.example

Simon P. Hayes
Partner
Tel: (416) 555-0172 ext. 102
Fax: (647) 555-0139
Email: simonhayes@vhlegal.example

Mark E. Dorsan
Barrister
Tel: (416) 555-0172 ext. 104
Fax: (647) 555-0139
Email: mdorsan@vhlegal.example

The back side should be crimson red (see mockup) with the logo (please update it to remove the & and the LLP, you can modify it a bit to make it tasteful if need be). Our new address is

82 Marlow Rd W, Suite 710
Toronto, ON M5K 0Z9

After our address, please also include our website www.vhlegal.example

Font styles to use
Sans Serif

Colors
ec2027
ffffff
000000

Requirements
Must have
• PLEASE NOTE: our firm's colour is more of a darker/crimson red, not a vibrant red.
• The front should have space for the lawyer's name, title, phone number (with extension), fax number, and email.
• If you're going to add those yourself, the info for the frontside is in the "Business Card Details" section (three lawyers that need their own cards).
Nice to have
• We like the backside of our current cards, just update it with our new address (one address now instead of 2), and a slightly modified logo (not a new logo altogether).
• The frontside should be refreshed with a better look (think minimalist, professional and modern), although still predominantly white-based background.
Should not have
• No scales of justice or other cheesy lawyer stereotype symbols! :-)

```html
<!DOCTYPE html>
<html lang="en">
<head>
<meta charset="utf-8">
<title>Volmont Hayes – Business Card Front</title>
<link rel="stylesheet" href="https://fonts.googleapis.com/css2?family=Barlow:wght@500;700&family=Questrial&display=swap">
<style>
  :root {
    --crimson: #c8202a;
    --ink: #111111;
    --paper: #ffffff;
  }
  * { margin: 0; padding: 0; box-sizing: border-box; }
  html, body {
    width: 1200px;
    height: 648px;
    overflow: hidden;
    background: var(--paper);
  }
  .card-front {
    position: relative;
    width: 1200px;
    height: 648px;
    background: var(--paper);
    color: var(--ink);
  }
  .firm-mark {
    position: absolute;
    top: 188px;
    right: 80px;
    display: flex;
    align-items: center;
    gap: 14px;
  }
  .firm-mark__dot {
    width: 22px;
    height: 22px;
    border-radius: 50%;
    background: var(--crimson);
  }
  .firm-mark__name {
    font-family: "Barlow", sans-serif;
    font-weight: 700;
    font-size: 40px;
    letter-spacing: 0.5px;
    color: var(--crimson);
  }
  .lawyer {
    position: absolute;
    left: 68px;
    top: 252px;
  }
  .lawyer__name {
    font-family: "Barlow", sans-serif;
    font-weight: 700;
    font-size: 34px;
    letter-spacing: 0.8px;
    color: var(--crimson);
    line-height: 1.1;
  }
  .lawyer__title {
    font-family: "Questrial", sans-serif;
    font-size: 28px;
    letter-spacing: 1px;
    color: var(--crimson);
    margin-top: 4px;
  }
  .contact {
    position: absolute;
    left: 68px;
    top: 458px;
    list-style: none;
    font-family: "Questrial", sans-serif;
    font-size: 29px;
    line-height: 39px;
    letter-spacing: 0.6px;
    color: var(--ink);
  }
  .contact__label {
    font-family: "Barlow", sans-serif;
    font-weight: 700;
  }
</style>
</head>
<body>
  <main class="card-front">
    <div class="firm-mark">
      <span class="firm-mark__dot"></span>
      <span class="firm-mark__name">Volmont Hayes</span>
    </div>

    <section class="lawyer">
      <h1 class="lawyer__name">Lorenzo T. Volmont</h1>
      <p class="lawyer__title">Partner</p>
    </section>

    <ul class="contact">
      <li><span class="contact__label">Tel:</span> (416) 555-0172 ext. 101</li>
      <li><span class="contact__label">Fax:</span> (647) 555-0139</li>
      <li><span class="contact__label">Email:</span> lvolmont@vhlegal.example</li>
    </ul>
  </main>
</body>
</html>
```